Luxury Real Estate Website, Midwest, United States

We need web design services for a luxury website. We need IDX Integration with our MLS. We want this to be a very simple website with amazing graphics. We want it to link up with our courier character account in order to generate leads through a "More Information" Pop up on the main page. We want the main page to be covered with one large graphic that is a rolling slideshow of active listings of $400,000 and up from the IDX Integration. We need this website to give a very exclusive and sleek look. Lots of black is good... I will upload our logos in Black and Silver. We will also need an "About" page that we are going to call "Qeno Info". We want our graphics to be extremely impressive. Keep in mind, we are a company in the Midwest of the United States, and our real estate has a different look than homes in California or Florida. We need graphics that are realistic for the Midwest, yet still high-end.
Target Market(s)
Luxury Homeowners in the Midwest United States. The graphics needs to be pristine.
Industry/Entity Type
Real Estate
Coding
Coded - Design and coding required
Number of Pages Required
3 page
Requirements
Must have
- Large graphics with IDX Integration. The photos of real estate need to represent real estate that is common in the Midwest, United States. We also need courier character integration. We need a pop up that is titled "My Free Market Analysis" that makes them fill out a contact form asking for Full Name, Email Address, Phone Number and Address. This needs to be a pop up on the front page and will integrate with our courier character account. We also need a page called "About Qe No Home". And another page where clients can download informational PDFs. The main component needs to be a front page search engine connected with the IDX to access active listings from our MLS. I attached our logos and a sample front page of a website. I would love for ours to look similar.
Nice to have
- Lake House photos on midwest lakes are a plus.
Should not have
- Should not have clutter. This website needs to be clean, luxurious and exclusive.

```html
<!DOCTYPE html>
<html lang="en">
<head>
<meta charset="utf-8">
<title>Hearthstone Realty Group</title>
<link href="https://fonts.googleapis.com/css2?family=Lato:wght@300;400;700;900&display=swap" rel="stylesheet">
<style>
:root{
  --ink:#111214;
  --text:#555a62;
  --muted:#8a8f98;
  --accent:#7f95b5;
  --accent-btn:#9aaac4;
  --navy:#26324d;
  --panel:#ececec;
  --line:#d3d6db;
  --footer:#121316;
  --white:#ffffff;
  --shade:rgba(8,9,12,.78);
}
*{box-sizing:border-box;margin:0;padding:0}
html,body{width:1200px;height:3871px;overflow:hidden}
body{position:relative;font-family:"Lato",sans-serif;color:var(--text);background:var(--white)}
.abs{position:absolute}
.ph{position:absolute}

/* header + hero */
.hero{left:0;top:0;width:1200px;height:692px;background:linear-gradient(160deg,#3c4a3a 0%,#2a3340 45%,#1b2029 100%);clip-path:polygon(0 0,100% 0,100% 560px,0 692px)}
.brand{left:98px;top:22px;display:flex;align-items:center;gap:14px;color:var(--white);font-weight:700;font-size:30px;letter-spacing:2px}
.brand .mark{width:22px;height:22px;background:var(--white)}
.nav{right:90px;top:82px;display:flex;gap:38px;font-size:14px;font-weight:700;letter-spacing:1px;color:var(--white)}
.hero-caption{left:0;width:1200px;top:325px;text-align:center;font-size:30px;color:var(--white);font-weight:300;letter-spacing:1px}
.hero-arrows{left:1052px;top:628px;display:flex;gap:14px}

/* welcome */
.welcome-photo{left:98px;top:779px;width:343px;height:457px;background:linear-gradient(180deg,#3b4756,#5a5245 60%,#3a4a3c)}
.welcome-text{left:480px;top:795px;width:622px}
.h-kicker{font-size:40px;font-weight:900;color:var(--ink);line-height:1.2}
.h-soft{font-size:40px;font-weight:300;color:var(--muted);line-height:1.2}
.body-copy{font-size:14px;line-height:1.95;color:var(--text);margin-top:22px}
.stats{display:flex;gap:0;margin-top:50px}
.stat{width:210px}
.stat b{display:block;font-size:34px;font-weight:300;color:var(--muted)}
.stat span{font-size:14px;color:var(--text)}

/* benefits */
.benefits{left:0;top:1321px;width:1200px;height:733px;background:var(--navy)}
.section-title{left:0;width:1200px;text-align:center;font-size:36px;color:var(--white);font-weight:400}
.rule{height:2px;width:90px;background:var(--accent)}
.benefit{width:300px;text-align:center;color:#c9cfdb}
.benefit .ring{margin:0 auto;border:2px solid #6e7b96;border-radius:50%;display:flex;align-items:center;justify-content:center}
.benefit h3{font-size:17px;font-weight:700;letter-spacing:1px;margin-top:22px;color:#dfe3ea}
.benefit p{font-size:13px;line-height:1.7;margin-top:10px;color:#9da6b8}

/* highlights */
.hl{left:98px;top:2128px;width:624px}
.hl-intro{font-size:14px;line-height:1.9;margin-top:16px}
.acc{margin-top:28px}
.acc-item{display:flex;align-items:center;gap:16px;height:48px;padding:0 16px;font-size:16px;color:var(--ink);border-bottom:1px solid var(--line)}
.acc-item.open{background:#f2f3f5;border:1px solid var(--line)}
.acc-body{font-size:13px;line-height:1.9;padding:18px 16px 22px}
.hl-photo{left:756px;top:2128px;width:346px;height:460px;background:linear-gradient(180deg,#7b8aa0,#8a5b46 55%,#4f5a44)}

/* gallery */
.gallery-title{left:0;width:1200px;top:2730px;text-align:center;font-size:38px}
.g{background:linear-gradient(160deg,#5e6a78,#3d4652)}
.g-caption{left:120px;top:3268px;font-size:15px;letter-spacing:2px;color:var(--white);font-weight:700}

/* footer */
.footer{left:0;top:3395px;width:1200px;height:476px;background:var(--footer);color:#a7abb3}
.f-text{font-size:13px;line-height:1.9}
.f-head{font-size:20px;color:var(--white);font-weight:700}
.f-links li{list-style:none;font-size:14px;height:41px;display:flex;align-items:center;gap:12px}
.f-links li::before{content:"";width:9px;height:9px;border:1.5px solid #8d929b;border-radius:50%}
.contact-row{display:flex;gap:18px;margin-bottom:26px}
.contact-row .c{width:40px;height:40px;border:1.5px solid #8d929b;border-radius:50%;flex:none;display:flex;align-items:center;justify-content:center}
.contact-row b{display:block;font-size:13px;color:var(--white);letter-spacing:1px}
.contact-row span{font-size:13px}
.social{display:flex;gap:12px}
.social i{width:30px;height:30px;border:1.5px solid #8d929b;border-radius:50%;display:block}
.copyright{left:0;width:1200px;top:3822px;text-align:center;font-size:13px;color:#8d929b}

/* overlay + modal */
.shade{left:0;top:0;width:1200px;height:3871px;background:var(--shade)}
.modal{left:227px;top:237px;width:746px;height:511px;background:var(--panel);box-shadow:0 10px 40px rgba(0,0,0,.5)}
.modal-art{left:18px;top:60px;width:285px;height:348px;background:radial-gradient(ellipse at 50% 45%,#c08a5c 0%,#6e8fc0 55%,rgba(236,236,236,0) 75%)}
.modal-title{left:325px;top:46px;font-size:32px;color:var(--accent);font-weight:400}
.modal-rule{left:325px;top:104px;width:98px;height:2px;background:var(--accent-btn)}
.field{left:325px;width:379px;height:44px;background:var(--white);border:1px solid #c7cbd1;font-size:14px;color:#555;padding:0 14px;display:flex;align-items:center}
.field.area{height:70px;align-items:flex-start;padding-top:12px}
.submit{left:325px;top:393px;width:121px;height:43px;background:var(--accent-btn);color:var(--white);font-size:15px;font-weight:700;display:flex;align-items:center;justify-content:center}
.close{left:946px;top:213px;width:48px;height:48px;border-radius:50%;background:#1e3f7a;border:3px solid var(--white);display:flex;align-items:center;justify-content:center}
</style>
</head>
<body>

<!-- hero -->
<div class="abs hero" role="img" aria-label="Slideshow photo of a Midwest lakefront luxury home"></div>
<div class="abs brand"><span>HEARTHSTONE</span><span class="mark"></span></div>
<nav class="abs nav"><span>HOME</span><span>QENO INFO</span><span>ABOUT QE NO HOME</span><span>DOWNLOADS</span><span>CONTACT US</span></nav>
<div class="abs hero-caption">Discover a lakefront home made for Midwest living</div>
<div class="abs hero-arrows">
  <svg width="18" height="30" viewBox="0 0 18 30"><path d="M15 3 3 15l12 12" fill="none" stroke="#fff" stroke-width="3"/></svg>
  <svg width="18" height="30" viewBox="0 0 18 30"><path d="M3 3l12 12L3 27" fill="none" stroke="#fff" stroke-width="3"/></svg>
</div>

<!-- welcome -->
<div class="ph welcome-photo" role="img" aria-label="Photo of a wooden lake house among trees"></div>
<div class="abs welcome-text">
  <div class="h-kicker">Welcome To</div>
  <div class="h-soft">Hearthstone Realty Group</div>
  <p class="body-copy">Nemo enim ipsam voluptatem quia voluptas sit aspernatur aut odit aut fugit sed quia consequuntur magni dolores eos qui ratione voluptatem sequi nesciunt neque porro quisquam est qui dolorem ipsum quia dolor sit amet consectetur adipisci velit sed quia non numquam eius modi tempora incidunt ut labore et dolore magnam aliquam quaerat voluptatem ut enim ad minima veniam quis nostrum exercitationem ullam corporis suscipit laboriosam.</p>
  <p class="body-copy" style="margin-top:14px">Neque porro quisquam est qui dolorem ipsum quia dolor sit amet consectetur adipisci velit sed quia non numquam eius modi tempora incidunt ut labore et dolore magnam aliquam quaerat voluptatem ut enim ad minima veniam quis nostrum exercitationem.</p>
  <div class="stats">
    <div class="stat"><b>24</b><span>Years Experience</span></div>
    <div class="stat" style="width:227px"><b>550</b><span>Projects Completed</span></div>
    <div class="stat"><b>2500</b><span>Workers Employed</span></div>
  </div>
</div>

<!-- benefits -->
<div class="abs benefits"></div>
<div class="abs section-title" style="top:1380px">Our Benefits</div>
<div class="abs rule" style="left:555px;top:1447px"></div>

<div class="abs benefit" style="left:90px;top:1496px">
  <div class="ring" style="width:114px;height:114px"><svg width="40" height="40" viewBox="0 0 40 40" fill="none" stroke="#8894ad" stroke-width="2"><rect x="6" y="10" width="28" height="22" rx="3"/><circle cx="20" cy="21" r="6"/></svg></div>
  <h3>SEHEAN A ISNN NSN</h3><p>Neque porro quisquam est dolorem ipsum quia dolor amet.</p>
</div>
<div class="abs benefit" style="left:810px;top:1496px">
  <div class="ring" style="width:114px;height:114px"><svg width="40" height="40" viewBox="0 0 40 40" fill="none" stroke="#8894ad" stroke-width="2"><rect x="6" y="8" width="28" height="20" rx="2"/><path d="M20 28v6M13 34h14"/></svg></div>
  <h3>SEHEAN A ISNN NSN</h3><p>Neque porro quisquam est dolorem ipsum quia dolor amet.</p>
</div>
<div class="abs benefit" style="left:450px;top:1558px">
  <div class="ring" style="width:248px;height:248px;background:#3a4663;border:none"><svg width="90" height="90" viewBox="0 0 90 90" fill="none" stroke="#1c2235" stroke-width="4"><rect x="18" y="12" width="54" height="68"/><path d="M30 24h8M52 24h8M30 38h8M52 38h8M30 52h8M52 52h8M38 80V66h14v14"/></svg></div>
  <h3>SEHEAN A ISNN NSN</h3><p>Neque porro quisquam est dolorem ipsum quia dolor amet.</p>
</div>
<div class="abs benefit" style="left:90px;top:1754px">
  <div class="ring" style="width:114px;height:114px"><svg width="40" height="40" viewBox="0 0 40 40" fill="none" stroke="#8894ad" stroke-width="2"><circle cx="18" cy="18" r="10"/><path d="M26 26l8 8"/></svg></div>
  <h3>SEHEAN A ISNN NSN</h3><p>Neque porro quisquam est dolorem ipsum quia dolor amet.</p>
</div>
<div class="abs benefit" style="left:810px;top:1754px">
  <div class="ring" style="width:114px;height:114px"><svg width="40" height="40" viewBox="0 0 40 40" fill="none" stroke="#8894ad" stroke-width="2"><path d="M6 20 20 8l14 12M10 17v15h20V17"/></svg></div>
  <h3>SEHEAN A ISNN NSN</h3><p>Neque porro quisquam est dolorem ipsum quia dolor amet.</p>
</div>

<!-- highlights -->
<div class="abs hl">
  <div class="h-kicker" style="font-size:38px">Our</div>
  <div class="h-soft" style="font-size:38px">Property Highlights</div>
  <p class="hl-intro">Nemo enim ipsam voluptatem quia voluptas sit aspernatur aut odit aut fugit sed quia consequuntur magni dolores eos qui ratione voluptatem sequi nesciunt.</p>
  <div class="acc">
    <div class="acc-item open"><svg width="18" height="18" viewBox="0 0 18 18"><path d="M3 9l4 4 8-8" fill="none" stroke="#555" stroke-width="2"/></svg>Property Description</div>
    <p class="acc-body">Nemo enim ipsam voluptatem quia voluptas sit aspernatur aut odit aut fugit sed quia consequuntur magni dolores eos qui ratione voluptatem sequi nesciunt.</p>
    <div class="acc-item"><svg width="18" height="18" viewBox="0 0 18 18"><path d="M3 9l4 4 8-8" fill="none" stroke="#333" stroke-width="2"/></svg>Living Space</div>
    <div class="acc-item"><svg width="18" height="18" viewBox="0 0 18 18"><path d="M3 9l4 4 8-8" fill="none" stroke="#333" stroke-width="2"/></svg>Other Info</div>
  </div>
</div>
<div class="ph hl-photo" role="img" aria-label="Photo of a brick lakeside house with a dock"></div>

<!-- gallery -->
<div class="abs gallery-title"><b style="color:var(--ink);font-weight:900">Our</b> <span style="color:var(--muted);font-weight:300">Gallery</span></div>
<div class="abs rule" style="left:555px;top:2800px"></div>
<div class="ph g" style="left:98px;top:2853px;width:444px;height:460px" role="img" aria-label="Photo of a stone estate home"></div>
<div class="abs g-caption">NEMO ENIM IPSAM VOLUPTATEM</div>
<div class="ph g" style="left:568px;top:2853px;width:534px;height:217px" role="img" aria-label="Photo of a white two-storey family home"></div>
<div class="ph g" style="left:568px;top:3096px;width:252px;height:217px" role="img" aria-label="Photo of a suburban house with lawn"></div>
<div class="ph g" style="left:846px;top:3096px;width:256px;height:217px" role="img" aria-label="Photo of a home exterior at dusk"></div>
<svg class="abs" style="left:38px;top:3066px" width="16" height="28" viewBox="0 0 16 28"><path d="M13 2 3 14l10 12" fill="none" stroke="#666" stroke-width="2.5"/></svg>
<svg class="abs" style="left:1146px;top:3066px" width="16" height="28" viewBox="0 0 16 28"><path d="M3 2l10 12L3 26" fill="none" stroke="#666" stroke-width="2.5"/></svg>

<!-- footer -->
<footer class="abs footer">
  <div class="abs brand" style="top:80px;font-size:30px"><span>HEARTHSTONE</span><span class="mark"></span></div>
  <p class="abs f-text" style="left:98px;top:188px;width:440px">Nemo enim ipsam voluptatem quia voluptas sit aspernatur aut odit aut fugit sed quia consequuntur magni dolores eos qui ratione voluptatem sequi nesciunt neque porro quisquam est qui dolorem.</p>
  <div class="abs social" style="left:98px;top:305px"><i></i><i></i><i></i><i></i></div>
  <div class="abs" style="left:624px;top:78px">
    <div class="f-head">Quick Links</div>
    <ul class="f-links" style="margin-top:26px"><li>Home</li><li>Qeno Info</li><li>About Qe No Home</li><li>Downloads</li><li>Contact Us</li></ul>
  </div>
  <div class="abs" style="left:870px;top:78px;width:260px">
    <div class="f-head">Contact Us</div>
    <div style="margin-top:28px">
      <div class="contact-row"><div class="c"><svg width="16" height="18" viewBox="0 0 16 18" fill="none" stroke="#bbb" stroke-width="1.6"><path d="M8 17s6-6 6-10A6 6 0 0 0 2 7c0 4 6 10 6 10z"/><circle cx="8" cy="7" r="2"/></svg></div><div><b>ADDRESS</b><span>1420 Harbor Lane, Lakeview</span></div></div>
      <div class="contact-row"><div class="c"><svg width="16" height="16" viewBox="0 0 16 16" fill="none" stroke="#bbb" stroke-width="1.6"><path d="M3 1h3l1.5 4L5.5 6.5a9 9 0 0 0 4 4L11 8.5l4 1.5v3a2 2 0 0 1-2 2A13 13 0 0 1 1 3a2 2 0 0 1 2-2z"/></svg></div><div><b>PHONE</b><span>Phone: 555-0142-386</span></div></div>
      <div class="contact-row"><div class="c"><svg width="16" height="12" viewBox="0 0 16 12" fill="none" stroke="#bbb" stroke-width="1.6"><rect x="1" y="1" width="14" height="10"/><path d="M1 1l7 6 7-6"/></svg></div><div><b>MAIL</b><span>info@hearthstonehomes.test</span></div></div>
    </div>
  </div>
</footer>
<div class="abs copyright">Copyright © 2018 Hearthstone Realty Group. All Rights Reserved</div>

<!-- overlay + popup -->
<div class="abs shade"></div>
<div class="abs modal">
  <div class="ph modal-art" role="img" aria-label="Illustration of a friendly courier character carrying a mail bag"></div>
  <div class="abs modal-title">My Free Market Analysis</div>
  <div class="abs modal-rule"></div>
  <div class="abs field" style="top:153px">Full Name</div>
  <div class="abs field" style="top:204px">Email Address</div>
  <div class="abs field" style="top:256px">Phone Number</div>
  <div class="abs field area" style="top:307px">Address</div>
  <div class="abs submit">Submit Now</div>
</div>
<div class="abs close"><svg width="16" height="16" viewBox="0 0 16 16"><path d="M3 3l10 10M13 3 3 13" stroke="#fff" stroke-width="3"/></svg></div>

</body>
</html>
```